Shipping and Logistics, Project

Project description : Company Profile

A total logistics company covering domestic / international freight forwarding, warehouse management services, haulage, supply chain management, transport management & distribution, procurement & assembly services, shipping, chartering & bunker services, project logistics & tax exemption consultancy, oil & gas logistics, halal logistics services & integrated logistics management. We’re a well-established and experienced freight forwarder in Kuala Lumpur, Malaysia. We specialize in customized value-added solution that optimizes your supply chain by trimming inventory, reducing logistics cost and enhancing your customer service levels.

As a member of the Worldwide Parcel and Carriage Alliance which comprise of 170 global freight agents in 80 countries that promotes great handling in cross-trade logistics and freighting. You could rely on our efficiency in handlings of export cargo (FCL, LCL, Bulk and Conventional) between our global network offices worldwide with a total scale of 10,000 groomed specialists in various logistics division working together to ensure delivery task meets with your expectation. With our dedicated qualified and experienced professionals, we are fully committed to serving our clients.

Our generic services are listed below for your reference:

• Air Freight
• Ocean Freight FCL & LCL
• Container Haulage
• Warehousing
• Transportation and Distribution within Malaysia and Thailand
• Cross-Border Road Line-hauls between Thailand, Malaysia, Singapore and Laos
• Customs Brokerage and Forwarding
• Project Cargo Freight Forwarding for setting up of new plants / factories and ad hoc heavy-lift
• Air-Sea-Road-Rail multi-modal options
• Import / Export / Storage / Documentation / Handling of DG / Hazmat
• Vessel and Aircraft Charters

Our Mission
Based on the motto “Quick, Reliable and Polite”, we are dedicated to upholding the following three points corporate philosophy:
1. Adhering to the principle that “the customer always comes first”.
2. Contributing to the development of the local community.
3. Making it our duty to be responsible and sincere.

Our Edge
• One-Stop Logistics Solutions
• Extensive Network Throughout Malaysia
• Highly Qualified and Experienced Pool of Professionals
• Comprehensive IT Solutions
• Innovative and Customer-focused Solutions
• Flexible and Consistent in Managing Exceptions
• Total Supply Chain Visibility

Target Market
1. We sell the logistics services to all the industry in Malaysia and Worldwide. (ONE Stop Logistics Solutions)

Competitor
1. TR Valmont
2. Corvessa Transport
3. Brandt + Loewe
4. FELRO
5. QTV
6. Routemarks
7. Ilto Logistics

Rules for Picking a Company Name
1. Unique and unforgettable
2. Avoid unusual spellings
3. Easy to pronounce and remember
4. Keep it simple
5. Make some sense
6. Give a clue

Rules for Picking a Company Logo
4. Keep it simple
5. Make some sense
6. Give a clue

1. Simplicity
2. Memorability
3. Originality
4. Modern Yet Timeless
5. Balance
6. Complementary
7. Versatility

Stationery Information
1. Company Name : ZENFreight Solutions Sdn Bhd
2. Company Registration : 2837165-W
3. Address : 42-08, Jalan Cempaka Indah 5, Taman Seri Bayu, 81300 Johor Bahru, Johor, Malaysia.
4. Name : Derek Tan
5. Position : Manager
6. Mobile No : (+6019) 4381907
7. Office No : (+607) 5218764
8. Fax No : Not Available
9. Email Address : derek.tan@zenfreight-solutions.example
10. Web Domain : www.zenfreight-solutions.example
11. Company Slogan : LINKING EVERY SHORE

Target Market(s)

Corporate Company

Industry/Entity Type

Shipping and Logistics Industry

Requirements
Must have
• Company Full Name : ZENFREIGHT SOLUTIONS SDN. BHD.
Nice to have
• Keep it simple and unforgettable ...

```html
<!DOCTYPE html>
<html lang="en">
<head>
<meta charset="utf-8">
<title>ZENFreight Solutions – Business Card</title>
<link rel="stylesheet" href="https://fonts.googleapis.com/css2?family=Montserrat:wght@500;700&family=Open+Sans:wght@400;600&display=swap">
<style>
  :root {
    --brand-blue: #2e88d8;
    --ink: #1d1d1f;
    --paper: #ffffff;
    --stage: #2b2b2d;
    --rule: #6aaee8;
  }
  * { box-sizing: border-box; margin: 0; padding: 0; }
  html, body { width: 1200px; height: 866px; overflow: hidden; }
  body {
    background: var(--stage);
    display: flex;
    flex-direction: column;
    align-items: center;
    justify-content: center;
    gap: 30px;
    font-family: "Open Sans", Arial, sans-serif;
  }
  .card {
    position: relative;
    width: 680px;
    height: 388px;
    overflow: hidden;
    box-shadow: 0 10px 24px rgba(0,0,0,.45);
  }

  /* Front */
  .card-front { background: var(--paper); color: var(--ink); }
  .holder { position: absolute; left: 48px; top: 52px; }
  .holder-name {
    font-family: "Montserrat", Arial, sans-serif;
    font-weight: 700; font-size: 30px; letter-spacing: 1px; line-height: 1;
  }
  .holder-name .surname { color: var(--brand-blue); }
  .holder-role {
    font-family: "Montserrat", Arial, sans-serif;
    font-weight: 500; font-size: 13px; letter-spacing: 1px; margin-top: 4px;
  }
  .contacts { list-style: none; margin-top: 16px; font-size: 13px; line-height: 1.55; }
  .contacts li { display: flex; align-items: center; gap: 8px; }
  .contacts svg { width: 13px; height: 13px; fill: none; stroke: var(--brand-blue); stroke-width: 1.6; flex: none; }

  .wordmark {
    position: absolute; display: flex; align-items: center; gap: 14px;
    font-family: "Montserrat", Arial, sans-serif; font-weight: 700;
    color: var(--brand-blue);
  }
  .wordmark .mark-square { background: var(--brand-blue); flex: none; }
  .wordmark .name-main { display: block; line-height: 1; }
  .wordmark .name-sub { display: block; letter-spacing: 3px; line-height: 1.3; }
  .card-front .wordmark { right: 44px; top: 90px; }
  .card-front .mark-square { width: 54px; height: 54px; }
  .card-front .name-main { font-size: 34px; letter-spacing: 1px; }
  .card-front .name-sub { font-size: 12.5px; }

  .front-rule { position: absolute; left: 300px; right: 44px; top: 222px; height: 1px; background: var(--rule); }
  .address {
    position: absolute; right: 44px; top: 234px; text-align: right;
    font-size: 14px; line-height: 1.45; font-style: normal;
  }
  .footer-band { position: absolute; left: 0; bottom: 0; width: 680px; height: 70px; }
  .registration {
    position: absolute; right: 44px; bottom: 12px;
    color: var(--paper); font-size: 13.5px; letter-spacing: .4px;
  }

  /* Back */
  .card-back { background: var(--brand-blue); color: var(--paper); }
  .card-back .wordmark { left: 50%; top: 118px; transform: translateX(-50%); color: var(--paper); gap: 18px; }
  .card-back .mark-square { width: 72px; height: 72px; background: var(--paper); }
  .card-back .name-main { font-size: 44px; letter-spacing: 1px; }
  .card-back .name-sub { font-size: 16px; letter-spacing: 4px; }
  .slogan {
    position: absolute; left: 60px; right: 60px; top: 272px;
    display: flex; align-items: center; gap: 16px;
    font-family: "Montserrat", Arial, sans-serif; font-weight: 500;
    font-size: 17px; letter-spacing: 2px; white-space: nowrap;
  }
  .slogan::before, .slogan::after { content: ""; flex: 1; height: 1px; background: rgba(255,255,255,.7); }
</style>
</head>
<body>

<section class="card card-front" aria-label="Business card front">
  <div class="holder">
    <h1 class="holder-name">DEREK <span class="surname">TAN</span></h1>
    <p class="holder-role">MANAGER</p>
    <ul class="contacts">
      <li><svg viewBox="0 0 14 14"><rect x="3.5" y="1" width="7" height="12" rx="1.2"/></svg>(+6019) 4381907</li>
      <li><svg viewBox="0 0 14 14"><path d="M3 1.5l2.5 2.5-1.5 1.6c.8 1.8 2.2 3.2 4 4l1.6-1.5 2.5 2.5-1.6 1.9C5.8 12.3 1.7 8.2 1.2 3.1z"/></svg>(+607) 5218764</li>
      <li><svg viewBox="0 0 14 14"><rect x="1" y="3" width="12" height="8"/><path d="M1 3l6 5 6-5"/></svg>derek.tan@zenfreight-solutions.example</li>
      <li><svg viewBox="0 0 14 14"><circle cx="7" cy="7" r="5.8"/><path d="M1.2 7h11.6M7 1.2c-3 3.5-3 8.1 0 11.6M7 1.2c3 3.5 3 8.1 0 11.6"/></svg>www.zenfreight-solutions.example</li>
    </ul>
  </div>

  <div class="wordmark">
    <span class="mark-square" aria-hidden="true"></span>
    <span class="wordmark-text">
      <span class="name-main">ZENFREIGHT</span>
      <span class="name-sub">SOLUTIONS SDN. BHD.</span>
    </span>
  </div>

  <div class="front-rule"></div>
  <address class="address">
    42-08, Jalan Cempaka Indah 5<br>
    Taman Seri Bayu<br>
    81300 Johor Bahru<br>
    Johor, Malaysia
  </address>

  <svg class="footer-band" viewBox="0 0 680 70" preserveAspectRatio="none" aria-hidden="true">
    <path d="M0 48 H220 L228 54 H0 Z" fill="#1d1d1f"/>
    <path d="M0 58 H250 C290 58 300 36 340 36 H680 V70 H0 Z" fill="#2e88d8"/>
  </svg>
  <p class="registration">Registration : 2837165-W</p>
</section>

<section class="card card-back" aria-label="Business card back">
  <div class="wordmark">
    <span class="mark-square" aria-hidden="true"></span>
    <span class="wordmark-text">
      <span class="name-main">ZENFREIGHT</span>
      <span class="name-sub">SOLUTIONS SDN. BHD.</span>
    </span>
  </div>
  <p class="slogan">LINKING EVERY SHORE</p>
</section>

</body>
</html>
```